Corvana Tongue Works, LLC

We need a business card that includes information about our business and conveys a reliable business that provides document translation services and interpreters for a variety of corporate and individual clients. We want to come across as professional, reliable, yet approachable. It should include the following on one side:

ESL / ENL Language Classes, Private Lessons, and Online Tutors
PLEXA Training and Testing
Translating & Interpreting Services
Contact us about Over-the-Phone Interpreting in over 200 languages
24/7/365
www.corvanatongue.example

The other side should include (555) 481-3062

Rhoda Pelling, President
482 Garnet Ave., Ste. 219
Indianapolis, IN 40917

Please add USA as part of the address. Also, please add rmpelling@corvanatongueworks.example as the e-mail address. Thank you.

Target Market(s)

Business professionals, their families, the international community

Industry/Entity Type

Business

Contact Information for Business Card

24/7/365
www.corvanatongue.example

(555) 481-3062

Rhoda Pelling, President
482 Garnet Ave., Ste. 219
Indianapolis, IN 40917
USA

Font styles to use
Sans Serif

Colors

Designer to choose colors to be used in the design.

Requirements
Must have
• See project description
• e-mail address and web address
• Phone number
Nice to have
• a globe
• physical address
Should not have
• Should not have the same color scheme as other agencies in our market in Indiana unless it is blue and black. No purple or yellow.

```html
<!DOCTYPE html>
<html lang="en">
<head>
<meta charset="utf-8">
<title>Corvana Tongue Works — Business Card</title>
<link rel="stylesheet" href="https://fonts.googleapis.com/css2?family=Roboto:wght@400;500&family=Open+Sans:wght@600&display=swap">
<style>
  :root {
    --bg: #4a433d;
    --card-black: #0b0b0c;
    --card-sheen: #2a2a2c;
    --brand-blue: #2f9ad8;
    --white: #ffffff;
    --text-light: #f2f2f2;
  }
  * { box-sizing: border-box; margin: 0; padding: 0; }
  html, body { width: 1200px; height: 930px; overflow: hidden; }
  body {
    background: var(--bg);
    font-family: "Roboto", Arial, sans-serif;
    position: relative;
  }
  .card {
    position: absolute;
    left: 250px;
    width: 700px;
    height: 400px;
    border-radius: 18px;
    overflow: hidden;
    background: linear-gradient(105deg, var(--card-black) 0%, var(--card-black) 30%, var(--card-sheen) 38%, var(--card-black) 48%, var(--card-black) 100%);
    box-shadow: 0 12px 30px rgba(0,0,0,0.45);
  }
  .card--back { top: 50px; }
  .card--front { top: 480px; }

  /* brand lockup */
  .brand { display: flex; align-items: center; gap: 16px; }
  .brand__disc {
    width: 96px; height: 96px; border-radius: 50%;
    flex: none;
  }
  .brand__name {
    font-family: "Open Sans", Arial, sans-serif;
    font-weight: 600;
    color: var(--brand-blue);
    line-height: 1.02;
    font-size: 36px;
  }

  /* back side */
  .card--back .brand { position: absolute; left: 170px; top: 52px; }
  .card--back .brand__disc { background: var(--white); border: 4px solid var(--card-black); outline: 3px solid var(--white); }
  .services {
    position: absolute; left: 0; right: 0; top: 200px;
    text-align: center; color: var(--text-light);
    font-size: 17px; line-height: 1.3; font-weight: 500;
  }
  .rule {
    position: absolute; left: 110px; right: 110px; top: 284px;
    height: 2px; background: var(--brand-blue);
  }
  .contact-note {
    position: absolute; left: 0; right: 0; top: 296px;
    text-align: center; color: var(--text-light);
    font-size: 17px; line-height: 1.3; font-weight: 500;
  }

  /* front side */
  .front-shape { position: absolute; inset: 0; }
  .card--front .brand { position: absolute; left: 424px; top: 112px; gap: 12px; }
  .card--front .brand__disc { width: 80px; height: 80px; background: var(--brand-blue); }
  .card--front .brand__name { font-size: 27px; }
  .person { position: absolute; left: 40px; top: 118px; color: var(--text-light); }
  .person__name {
    color: var(--brand-blue); font-weight: 500; font-size: 32px;
    letter-spacing: 0.5px; text-transform: uppercase;
  }
  .person__title { font-size: 17px; margin-top: 2px; }
  .person__address { font-size: 17px; line-height: 1.3; margin-top: 14px; }
  .contacts { list-style: none; margin-top: 16px; font-size: 17px; line-height: 1.45; }
  .contacts li { display: flex; align-items: center; gap: 10px; }
  .contacts svg { width: 14px; height: 14px; flex: none; }
  .web-domain { color: var(--brand-blue); }
</style>
</head>
<body>

<section class="card card--back" aria-label="Card back">
  <div class="brand">
    <span class="brand__disc"></span>
    <span class="brand__name">Corvana<br>Tongue<br>Works LLC</span>
  </div>
  <p class="services">
    ESL / ENL Language Classes, Private Lessons, and Online Tutors<br>
    PLEXA Training and Testing<br>
    Translating &amp; Interpreting Services
  </p>
  <div class="rule"></div>
  <p class="contact-note">
    Contact us about Over-the-Phone Interpreting in over 200 languages<br>
    24/7/365
  </p>
</section>

<section class="card card--front" aria-label="Card front">
  <svg class="front-shape" viewBox="0 0 700 400" aria-hidden="true">
    <circle cx="636" cy="150" r="266" fill="none" stroke="var(--brand-blue)" stroke-width="4"/>
    <circle cx="642" cy="150" r="260" fill="var(--white)"/>
  </svg>
  <div class="brand">
    <span class="brand__disc"></span>
    <span class="brand__name">Corvana<br>Tongue<br>Works LLC</span>
  </div>
  <div class="person">
    <h1 class="person__name">Rhoda Pelling</h1>
    <p class="person__title">President</p>
    <p class="person__address">482 Garnet Ave., Ste. 219<br>Indianapolis, IN 40917 USA</p>
    <ul class="contacts">
      <li>
        <svg viewBox="0 0 24 24"><path fill="var(--brand-blue)" d="M6.6 10.8a15 15 0 0 0 6.6 6.6l2.2-2.2c.3-.3.7-.4 1-.2 1.1.4 2.3.6 3.6.6.6 0 1 .4 1 1V20c0 .6-.4 1-1 1A17 17 0 0 1 3 4c0-.6.4-1 1-1h3.5c.6 0 1 .4 1 1 0 1.3.2 2.5.6 3.6.1.3 0 .7-.2 1z"/></svg>
        (555) 481-3062
      </li>
      <li>
        <svg viewBox="0 0 24 24"><rect x="2" y="5" width="20" height="14" rx="2" fill="none" stroke="var(--brand-blue)" stroke-width="2"/><path d="M3 6l9 7 9-7" fill="none" stroke="var(--brand-blue)" stroke-width="2"/></svg>
        rmpelling@corvanatongueworks.example
      </li>
      <li>
        <svg viewBox="0 0 24 24"><circle cx="12" cy="12" r="9" fill="none" stroke="var(--brand-blue)" stroke-width="2"/><ellipse cx="12" cy="12" rx="4" ry="9" fill="none" stroke="var(--brand-blue)" stroke-width="2"/><path d="M3 12h18" stroke="var(--brand-blue)" stroke-width="2"/></svg>
        <span>www.<span class="web-domain">corvanatongue</span>.example</span>
      </li>
    </ul>
  </div>
</section>

</body>
</html>
```